Fee Detective - Website Design

Create website designs for new FeeDetective.com web application.
We are looking for a clean, playful design based on the attached wireframes and the images we have collected on our PinVault board for inspiration : https://app.pinvault-example.net/7QrTb2kZw4Xc81?p=3Hyd9mLe5Rf
Users of the site will want to be able to quickly run a search using the transaction descriptor they want to identify and see any matching merchants. If they don't get a match then we need then to be able to easily provide further details so we can try and find a match for them
Target Market(s)
Anyone with a bank account
Number of Pages Required
5+ page
Requirements
Must have
- Clean yet playful design, incorporating the themes from our pinvault board

```html
<!DOCTYPE html>
<html lang="en">
<head>
<meta charset="utf-8">
<title>Fee Detective – Website Design</title>
<link href="https://fonts.googleapis.com/css2?family=Mulish:wght@400;500;600;700;800&display=swap" rel="stylesheet">
<style>
  :root {
    --stage: #3d0f57;
    --brand-pink: #d1145a;
    --ink: #111111;
    --muted: #8a8a8a;
    --link: #e0306a;
    --lime: #a2c21b;
    --white: #ffffff;
    --line: #dedede;
  }
  * { box-sizing: border-box; margin: 0; padding: 0; }
  html, body {
    width: 1200px; height: 2309px; overflow: hidden;
    background: var(--stage);
    font-family: "Mulish", sans-serif;
  }
  .screen {
    position: absolute; left: 63px; width: 1049px; height: 696px;
    overflow: hidden;
    background:
      radial-gradient(circle at 90% 34%, rgba(255,236,190,0.75) 0, rgba(255,246,220,0.35) 16%, transparent 32%),
      radial-gradient(ellipse at 34% 46%, rgba(214,238,184,0.85) 0, rgba(228,244,208,0.5) 22%, transparent 45%),
      radial-gradient(ellipse at 56% 78%, rgba(206,236,246,0.9) 0, transparent 28%),
      linear-gradient(135deg, #ffffff 0%, #fbfdf6 50%, #fffdf3 100%);
  }
  .screen--home { top: 56px; }
  .screen--suggest { top: 797px; }
  .screen--nomatch { top: 1546px; }

  .title {
    position: absolute; left: 0; right: 0; text-align: center;
    font-size: 64px; font-weight: 700; color: var(--ink); letter-spacing: 0.5px;
    line-height: 1;
  }
  .title .accent { color: var(--brand-pink); }
  .tagline {
    position: absolute; left: 0; right: 0; text-align: center;
    font-size: 18px; font-weight: 500; line-height: 32px; color: var(--ink);
  }
  .search {
    position: absolute; left: 194px; width: 662px; height: 52px;
    background: var(--white); border-radius: 26px;
    box-shadow: 0 4px 14px rgba(0,0,0,0.06);
    padding: 0 28px; display: flex; align-items: center; justify-content: space-between;
    font-size: 12.5px; color: var(--muted);
  }
  .search .value { text-transform: uppercase; font-weight: 500; }
  .chevron { width: 10px; height: 7px; }
  .dropdown {
    position: absolute; left: 194px; width: 662px; height: 156px;
    background: var(--white); border-radius: 22px;
    box-shadow: 0 4px 14px rgba(0,0,0,0.06);
    font-size: 11px; color: var(--muted); font-weight: 500;
  }
  .dropdown .field {
    height: 46px; margin: 0 22px 0 16px; border-bottom: 1px solid var(--line);
    display: flex; align-items: center; justify-content: space-between; padding: 0 6px 0 12px;
  }
  .dropdown .options { list-style: none; padding: 16px 28px 0; }
  .dropdown .options li { line-height: 26px; }
  .help-link {
    position: absolute; left: 0; right: 0; text-align: center;
    font-size: 12.5px; color: var(--link);
  }
  .result-title {
    position: absolute; left: 0; right: 0; text-align: center;
    font-size: 15px; font-weight: 700; color: var(--ink);
  }
  .result-text {
    position: absolute; left: 190px; width: 670px; text-align: center;
    font-size: 10.5px; line-height: 19px; color: var(--ink);
  }
  .cta {
    position: absolute; left: 425px; width: 239px; height: 35px;
    background: var(--lime); border-radius: 18px;
    display: flex; align-items: center; justify-content: center;
    font-size: 15px; font-weight: 700; color: var(--ink);
  }
  .skyline {
    position: absolute; left: 0; right: 0; bottom: 0; height: 170px;
    background:
      linear-gradient(to top, rgba(255,255,255,0) 0, rgba(255,255,255,0) 100%),
      linear-gradient(90deg, rgba(255,255,255,0) 0%, #3a5a96 12%, #c43a78 32%, #e8306a 50%, #c43a78 68%, #3a5a96 88%, rgba(255,255,255,0) 100%);
    -webkit-mask-image: linear-gradient(to top, #000 35%, rgba(0,0,0,0.5) 70%, transparent 100%);
    mask-image: linear-gradient(to top, #000 35%, rgba(0,0,0,0.5) 70%, transparent 100%);
  }
</style>
</head>
<body>

<section class="screen screen--home">
  <h1 class="title" style="top:128px"><span class="accent">Fee</span> Detective</h1>
  <p class="tagline" style="top:221px">Helping you identify those odd and sometimes surprising charges on your<br>bank statements and transaction feeds!</p>
  <div class="search" style="top:321px">
    <span>Enter your transaction descriptor...</span>
    <svg class="chevron" viewBox="0 0 10 7"><path d="M1 1l4 4 4-4" fill="none" stroke="#333" stroke-width="1.4"/></svg>
  </div>
  <p class="help-link" style="top:394px">What is a Transaction Descriptor?</p>
  <div class="skyline" role="img" aria-label="Pink and blue city skyline illustration"></div>
</section>

<section class="screen screen--suggest">
  <h1 class="title" style="top:128px"><span class="accent">Fee</span> Detective</h1>
  <p class="tagline" style="top:221px">Helping you identify those odd and sometimes surprising charges on your<br>bank statements and transaction feeds!</p>
  <div class="dropdown" style="top:322px">
    <div class="field">
      <span>GROCE</span>
      <svg class="chevron" viewBox="0 0 10 7"><path d="M1 1l4 4 4-4" fill="none" stroke="#333" stroke-width="1.4"/></svg>
    </div>
    <ul class="options">
      <li>GROCERMART PTY LTD ST IVES AU</li>
      <li>GROCERMART ONLINE SERVICES AU220223</li>
      <li>GROCERWEAR CLOTHING CO SYDNEY</li>
    </ul>
  </div>
  <div class="skyline" role="img" aria-label="Pink and blue city skyline illustration"></div>
</section>

<section class="screen screen--nomatch">
  <h1 class="title" style="top:72px"><span class="accent">Fee</span> Detective</h1>
  <p class="tagline" style="top:165px">Helping you identify those odd and sometimes surprising charges on your<br>bank statements and transaction feeds!</p>
  <div class="search" style="top:267px">
    <span class="value">GROCERMART PTY LTD ST IVES AU</span>
    <svg class="chevron" viewBox="0 0 10 7"><path d="M1 1l4 4 4-4" fill="none" stroke="#333" stroke-width="1.4"/></svg>
  </div>
  <p class="help-link" style="top:340px">What is a Transaction Descriptor?</p>
  <h2 class="result-title" style="top:378px">Hmmm, we couldn't find a match!</h2>
  <p class="result-text" style="top:411px">Couldn't find a match? Help us Crowd Source more data by clicking the button below and providing a few details so we can help find it and make it available to everyone.</p>
  <div class="cta" style="top:472px">Help improve our results</div>
  <div class="skyline" role="img" aria-label="Pink and blue city skyline illustration"></div>
</section>

</body>
</html>
```